Quarrybend Marble & Tile Needs a Business Card

Attached you will find your logo, my photo and design guidelines for a new business card. The final design will need two separate files to create an embossed card. The cards will be printed by www.plinkprint.com (Instructions below)
Format is the Plink SQUARE card
Quarrybend Marble And Tile is a brick and mortar, retail stone and tile shop.
One the front:
Quarrybend Marble And Tile
Dorian Fesslock
Owner
24807 Hollis Verdant Blvd
Suite P & R
Charlotte, NC 28193
Cell: 704-583-7142
Web: www.QuarrybendMarbleAndTile.com
(Make each word of the domain a different or alternating color)
On the back;
Something that shows beautiful colorful tile
Follow the design guide closely please. For more information see this page that describes creating the spot gloss file: https://www.plinkprint.com/us/business-cards/design-guidelines-spot-gloss
The logo is what we would like to have raised spot glossed.
Format is the Plink SQUARE card. See attahced guidlines.

```html
<!DOCTYPE html>
<html lang="en">
<head>
<meta charset="utf-8">
<title>Quarrybend Marble &amp; Tile – Square Business Card</title>
<link href="https://fonts.googleapis.com/css2?family=Montserrat:wght@400;500&family=Tinos:wght@400;700&display=swap" rel="stylesheet">
<style>
  :root {
    --page: #c4c5c7;
    --paper: #ffffff;
    --ink: #1f2833;
    --navy: #26313d;
    --gold: #d0912f;
    --rust: #b4532a;
    --sage: #7d8470;
    --slate: #4f6273;
    --night: #0c0b0a;
    --photo-a: #d9d2ca;
    --photo-b: #6e6259;
  }
  * { box-sizing: border-box; margin: 0; padding: 0; }
  html, body { width: 1200px; height: 900px; overflow: hidden; }
  body { background: var(--page); position: relative; font-family: "Montserrat", sans-serif; color: var(--ink); }

  .card { position: absolute; width: 470px; height: 471px; overflow: hidden; }
  .card-front { left: 107px; top: 215px; background: var(--paper); }
  .card-back { left: 616px; top: 214px; background: var(--night); }
  .gold-band { position: absolute; left: 0; right: 0; bottom: 0; height: 15px; background: var(--gold); }
  .card-back .gold-band { height: 17px; }

  .brand { position: absolute; text-align: center; font-family: "Montserrat", sans-serif; font-weight: 500; }
  .brand-mark { display: block; margin: 0 auto; background: var(--gold); }
  .brand-name { display: block; letter-spacing: 0.12em; white-space: nowrap; }
  .brand-sub { display: block; letter-spacing: 0.34em; white-space: nowrap; }

  .card-front .brand { left: 228px; width: 206px; top: 98px; color: var(--navy); }
  .card-front .brand-mark { width: 14px; height: 14px; margin-bottom: 18px; }
  .card-front .brand-name { font-size: 22px; line-height: 26px; }
  .card-front .brand-rule { height: 1px; background: var(--gold); margin: 5px 4px 6px; }
  .card-front .brand-sub { font-size: 11px; }

  .photo { position: absolute; left: 27px; top: 265px; width: 165px; height: 164px; border: 1.5px solid var(--gold); background: var(--paper); padding: 7px 8px; }
  .photo-fill { width: 100%; height: 100%; background: linear-gradient(180deg, var(--photo-a) 0%, #b6a89b 45%, var(--photo-b) 100%); }

  .contact { position: absolute; left: 198px; top: 258px; width: 268px; }
  .person-name { font-family: "Tinos", serif; font-weight: 700; font-size: 24px; line-height: 28px; color: #111; }
  .person-role { font-size: 14px; color: var(--gold); line-height: 17px; }
  .address { margin-top: 15px; margin-left: 4px; font-size: 13.5px; line-height: 17.5px; color: #1a1a1a; }
  .line { font-family: "Tinos", serif; font-size: 15px; display: flex; align-items: center; margin-left: 4px; line-height: 24px; color: #1a1a1a; white-space: nowrap; }
  .line svg { width: 13px; height: 13px; margin-right: 8px; flex: none; }
  .line-phone { margin-top: 9px; font-size: 17px; }
  .web-gold { color: var(--gold); }
  .web-rust { color: var(--rust); }

  .tile-field {
    position: absolute; inset: 0 0 17px 0;
    background:
      radial-gradient(circle at 50% 33%, rgba(208,145,47,0.30) 0%, rgba(180,83,42,0.18) 14%, rgba(79,98,115,0.12) 26%, transparent 40%),
      radial-gradient(circle at 18% 80%, rgba(125,132,112,0.14) 0%, transparent 35%),
      radial-gradient(circle at 85% 15%, rgba(180,83,42,0.14) 0%, transparent 35%),
      radial-gradient(circle at 85% 85%, rgba(79,98,115,0.16) 0%, transparent 35%),
      radial-gradient(circle at 12% 15%, rgba(208,145,47,0.12) 0%, transparent 35%),
      var(--night);
  }
  .card-back .brand { left: 0; right: 0; top: 236px; color: #fff; }
  .card-back .brand-mark { width: 18px; height: 18px; margin-bottom: 24px; }
  .card-back .brand-name { font-size: 33px; line-height: 38px; }
  .card-back .brand-rule { height: 1px; background: var(--gold); margin: 8px 95px 10px; }
  .card-back .brand-sub { font-size: 17px; }
</style>
</head>
<body>
  <section class="card card-front">
    <div class="brand">
      <span class="brand-mark"></span>
      <span class="brand-name">QUARRYBEND</span>
      <div class="brand-rule"></div>
      <span class="brand-sub">MARBLE &amp; TILE</span>
    </div>

    <div class="photo"><div class="photo-fill" role="img" aria-label="Portrait photo of Dorian Fesslock, owner"></div></div>

    <div class="contact">
      <h1 class="person-name">Dorian Fesslock</h1>
      <p class="person-role">Owner</p>
      <p class="address">24807 Hollis Verdant Blvd<br>Suite P &amp; R<br>Charlotte, NC 28193</p>
      <p class="line line-phone">
        <svg viewBox="0 0 14 14" aria-hidden="true"><path d="M1 5c0-2 2-3 6-3s6 1 6 3v1h-3V4.5H4V6H1z M3 7h8l2 5H1z" fill="#d0912f"/></svg>
        704-583-7142
      </p>
      <p class="line">
        <svg viewBox="0 0 14 14" aria-hidden="true"><circle cx="7" cy="7" r="6" fill="#d0912f"/><path d="M4 3.5c2 0 2 2 3.5 2S8 8 6 8.5 4 11 4 11M9 3c0 1.5 1.5 2 2.5 2" stroke="#fff" stroke-width="1.2" fill="none"/></svg>
        <span>www.<span class="web-gold">Quarrybend</span>Marble<span class="web-rust">And</span>Tile.com</span>
      </p>
    </div>

    <div class="gold-band"></div>
  </section>

  <section class="card card-back">
    <div class="tile-field" role="img" aria-label="Colourful mosaic tile pattern in rust, gold, sage and slate on black"></div>
    <div class="brand">
      <span class="brand-mark"></span>
      <span class="brand-name">QUARRYBEND</span>
      <div class="brand-rule"></div>
      <span class="brand-sub">MARBLE &amp; TILE</span>
    </div>
    <div class="gold-band"></div>
  </section>
</body>
</html>
```